RWT Fittings Ltd Business Cards

We need a business card with our business logo. We provide window and door installations on high-rises in west coast British Colombia, Canada.

I would like my business information and details on one side of the card, and the other side the company name with logo

Target Market(s)

General Contractors

Industry/Entity Type

Construction

Contact Information for Business Card

one side i want my company name and logo in the dark theme logo that i provided

Requirements
Must have
• Marco Peltieri, 16045518293, RWTFittings@mailbox-demo.com, 1407-5194 Linden Row Burnaby BC, V5H 2K9, Owner & Manager

```html
<!DOCTYPE html>
<html lang="en">
<head>
<meta charset="utf-8">
<title>RWT Fittings Ltd – Business Cards</title>
<link rel="stylesheet" href="https://fonts.googleapis.com/css2?family=Roboto:wght@400;500;700&display=swap">
<style>
  :root {
    --stage: #2b2c31;
    --card: #1f2026;
    --blue: #29abe2;
    --grey: #a3a3a5;
    --text: #f2f2f2;
    --soft: #cfd0d2;
  }
  html, body {
    margin: 0;
    width: 1200px;
    height: 780px;
    overflow: hidden;
    background: var(--stage);
    font-family: "Roboto", Arial, sans-serif;
  }
  .stage {
    position: relative;
    width: 1200px;
    height: 780px;
    display: flex;
    align-items: center;
    justify-content: center;
    gap: 40px;
  }
  .card {
    position: relative;
    width: 540px;
    height: 310px;
    background: var(--card);
    border-radius: 18px;
    overflow: hidden;
    box-shadow: 0 18px 40px rgba(0,0,0,.45);
  }
  .card__bands {
    position: absolute;
    inset: 0;
    width: 100%;
    height: 100%;
  }
  .band--blue { fill: var(--blue); }
  .band--grey { fill: var(--grey); }

  .brand {
    position: absolute;
    display: flex;
    align-items: center;
    gap: 14px;
    color: var(--blue);
    font-weight: 700;
    letter-spacing: .02em;
    white-space: nowrap;
  }
  .brand__mark {
    background: var(--blue);
    flex: none;
  }
  .card--front .brand {
    left: 70px;
    top: 112px;
    font-size: 36px;
  }
  .card--front .brand__mark { width: 44px; height: 44px; }

  .card--back .brand {
    left: 28px;
    top: 124px;
    font-size: 18px;
    gap: 9px;
  }
  .card--back .brand__mark { width: 22px; height: 22px; }

  .divider {
    position: absolute;
    left: 266px;
    top: 58px;
    width: 1px;
    height: 148px;
    background: var(--soft);
  }
  .contact {
    position: absolute;
    left: 290px;
    top: 56px;
    color: var(--text);
  }
  .contact__name {
    margin: 0;
    font-size: 27px;
    font-weight: 700;
    line-height: 1;
    letter-spacing: -.01em;
  }
  .contact__first { color: var(--blue); }
  .contact__last { color: var(--soft); }
  .contact__role {
    margin: 4px 0 22px;
    font-size: 13px;
    font-weight: 500;
  }
  .contact__list {
    list-style: none;
    margin: 0;
    padding: 0;
    font-size: 13px;
  }
  .contact__item {
    display: flex;
    align-items: center;
    gap: 8px;
    margin-bottom: 6px;
  }
  .contact__icon { width: 13px; height: 13px; flex: none; }
  .contact__icon path, .contact__icon rect { fill: none; stroke: var(--blue); stroke-width: 2; stroke-linejoin: round; stroke-linecap: round; }

  .address {
    position: absolute;
    left: 28px;
    top: 222px;
    margin: 0;
    color: var(--text);
    font-size: 14px;
    font-weight: 500;
    font-style: normal;
    white-space: nowrap;
  }
</style>
</head>
<body>
<main class="stage">

  <section class="card card--front" aria-label="Card front">
    <svg class="card__bands" viewBox="0 0 540 310" preserveAspectRatio="none" aria-hidden="true">
      <polygon class="band--grey" points="300,256 540,218 540,240 322,270"/>
      <polygon class="band--blue" points="0,296 250,296 310,264 334,264 262,310 0,310"/>
    </svg>
    <div class="brand"><span class="brand__mark"></span>RWT FITTINGS LTD</div>
  </section>

  <section class="card card--back" aria-label="Card back">
    <svg class="card__bands" viewBox="0 0 540 310" preserveAspectRatio="none" aria-hidden="true">
      <polygon class="band--grey" points="300,256 540,218 540,240 322,270"/>
      <polygon class="band--blue" points="0,296 250,296 310,264 334,264 262,310 0,310"/>
    </svg>

    <div class="brand"><span class="brand__mark"></span>RWT FITTINGS LTD</div>

    <div class="divider"></div>

    <div class="contact">
      <h1 class="contact__name"><span class="contact__first">Marco</span> <span class="contact__last">Peltieri</span></h1>
      <p class="contact__role">Owner &amp; Manager</p>
      <ul class="contact__list">
        <li class="contact__item">
          <svg class="contact__icon" viewBox="0 0 14 14" aria-hidden="true"><path d="M3 1.5l2 2.5-1.3 1.6a8 8 0 0 0 4.7 4.7L10 9l2.5 2-1.2 1.8C6 12.5 1.5 8 1.2 2.7z"/></svg>
          1604 551 8293
        </li>
        <li class="contact__item">
          <svg class="contact__icon" viewBox="0 0 14 14" aria-hidden="true"><rect x="1" y="3" width="12" height="8.5" rx="1"/><path d="M1.5 3.5L7 8l5.5-4.5"/></svg>
          RWTFittings@mailbox-demo.com
        </li>
      </ul>
    </div>

    <address class="address">1407-5194 Linden Row Burnaby BC, V5H 2K9</address>
  </section>

</main>
</body>
</html>
```